Interior designer needs a power point template design

I need a template PowerPoint design for my client presentations. The presentations I prepare for my clients usually include the furniture project, the detail of the selected furniture, and the costs. There are a lot of images I insert. What I need is to have a template that I can use for all my presentations, where from time to time I will insert the specific images and descriptions I want to insert. What will always be the same will be the cover, the colors, the font, and the design of the internal sections.
I already have my logo that I would like to insert on each page of the presentation (in small size).
In summary, I need:
- basic template design
- cover with an image chosen by Pictavale photo
- design an internal section/chapter
- internal page design.

I like the clolors of pink and brown <8please see image attached)
Images (will come from Pictavale photo)
● entrance/hall
● living room
● dining room
● Bathroom
● Closet
● Kids room
● Master bedroom
● Master bathroom
● Kitchen
● Office
● Laundry
● Balcony or Terrace

Target Market(s)

Customers (both residential and commercial projects)

Industry/Entity Type

interior design

Font styles to use
Other font styles liked:
• I like courier new

Requirements
Must have
• beautiful design
Should not have
• animations

```html
<!DOCTYPE html>
<html lang="en">
<head>
<meta charset="utf-8">
<title>Casa Lumen – Presentation Template</title>
<link rel="stylesheet" href="https://fonts.googleapis.com/css2?family=Arimo:wght@400;700&display=swap">
<style>
  :root {
    --stage: #5f5e61;
    --paper: #ffffff;
    --ink: #111111;
    --body-ink: #222222;
    --line: #2a2a2a;
    --wood-light: #dcc7a8;
    --wood-mid: #c8ae8c;
    --cream: #fbeed6;
    --sand: #d9b879;
    --blush: #f5ecea;
    --slate: #3f4a55;
  }
  * { box-sizing: border-box; margin: 0; padding: 0; }
  html, body { width: 1200px; height: 1065px; overflow: hidden; }
  body {
    background: var(--stage);
    font-family: "Arimo", Arial, sans-serif;
    color: var(--ink);
    position: relative;
  }
  .slide {
    position: absolute;
    width: 525px;
    height: 296px;
    background: var(--paper);
    overflow: hidden;
  }
  .col-a { left: 63px; }
  .col-b { left: 612px; }
  .row-1 { top: 67px; }
  .row-2 { top: 385px; }
  .row-3 { top: 702px; }

  .page-title {
    position: absolute;
    font-size: 23px;
    line-height: 28px;
    font-weight: 400;
    letter-spacing: 0.3px;
    text-transform: uppercase;
  }
  .page-text {
    position: absolute;
    font-size: 8.8px;
    line-height: 16.2px;
    color: var(--body-ink);
    text-align: justify;
  }
  .page-list {
    position: absolute;
    font-size: 8.8px;
    line-height: 16.2px;
    font-weight: 700;
    color: var(--body-ink);
  }

  .brand {
    position: absolute;
    display: flex;
    flex-direction: column;
    align-items: center;
    gap: 5px;
    font-family: "Arimo", Arial, sans-serif;
    font-weight: 400;
    color: var(--ink);
    text-transform: uppercase;
    text-align: center;
  }
  .brand-dot {
    border: 1px solid var(--line);
    border-radius: 50%;
  }
  .brand-large { font-size: 13px; letter-spacing: 1.5px; line-height: 14px; }
  .brand-large .brand-dot { width: 50px; height: 50px; }
  .brand-small { font-size: 7px; letter-spacing: 0.8px; line-height: 8px; }
  .brand-small .brand-dot { width: 28px; height: 28px; }

  .photo { position: absolute; }

  /* Cover */
  .cover-photo {
    left: 109px; top: 0; width: 416px; height: 296px;
    background: linear-gradient(160deg, var(--wood-light) 0%, #d2bb9a 45%, var(--wood-mid) 100%);
  }
  .cover-panel {
    position: absolute; left: 0; top: 153px; width: 339px; height: 143px;
    background: var(--paper);
  }

  /* Laundry */
  .laundry-art { position: absolute; left: 222px; top: 91px; width: 303px; height: 205px; }

  /* Bedroom circle */
  .sketch-lines { position: absolute; left: 0; top: 0; }
  .bedroom-photo {
    left: 56px; top: 59px; width: 176px; height: 176px; border-radius: 50%;
    background: radial-gradient(circle at 50% 45%, #8d949a 0%, #6b7278 40%, #b9bcc0 70%, #c79a62 100%);
  }

  /* Closet circle */
  .closet-frame {
    position: absolute; left: 10px; top: 23px; width: 248px; height: 248px;
    border-radius: 50%; background: #2b2b2d;
  }
  .closet-photo {
    left: 16px; top: 27px; width: 240px; height: 240px; border-radius: 50%;
    background: linear-gradient(180deg, #e9e9ea 0%, #4a4b52 18%, #e6e6e8 30%, #55565e 48%, #3a3b40 78%, #ededee 100%);
  }

  /* Bedroom view */
  .room-photo {
    left: 260px; top: 0; width: 265px; height: 296px;
    background: linear-gradient(180deg, #dcdde0 0%, #e4e5e8 45%, var(--slate) 62%, #55606a 76%, #b07a45 88%, #9c6a3a 100%);
  }
  .room-brand-panel {
    position: absolute; left: 232px; top: 0; width: 44px; height: 66px; background: var(--paper);
  }

  /* Wardrobe */
  .wardrobe-photo {
    left: 261px; top: 0; width: 264px; height: 296px;
    background: linear-gradient(180deg, var(--blush) 0%, #ece2df 35%, #9e9593 55%, #6e6765 75%, var(--blush) 100%);
  }
  .wardrobe-brand-panel {
    position: absolute; left: 232px; top: 0; width: 45px; height: 66px; background: var(--paper);
  }
</style>
</head>
<body>

<!-- Cover -->
<section class="slide col-a row-1 slide-cover">
  <div class="photo cover-photo" role="img" aria-label="Cover image: woman in a dotted dress with a handbag among autumn leaves on light wood"></div>
  <div class="brand brand-large" style="left: 14px; top: 22px; width: 82px;">
    <span class="brand-dot"></span>
    <span>Casa<br>Lumen</span>
  </div>
  <div class="cover-panel">
    <h1 class="page-title" style="left: 32px; top: 20px;">Welcome</h1>
    <p class="page-text" style="left: 32px; top: 60px; width: 272px;">Lorem ipsum dolor sit amet, consectetur adipiscing elit, sed do eiusmod tempor incididunt ut labore et dolore magna aliqua. Quis ipsum suspendisse ultrices gravida. Risus commodo viverra maecenas accumsan lacus vel facilisis.</p>
  </div>
</section>

<!-- Laundry section -->
<section class="slide col-b row-1 slide-laundry">
  <h2 class="page-title" style="left: 24px; top: 36px;">Page title<br>here</h2>
  <p class="page-text" style="left: 24px; top: 102px; width: 197px;">Lorem ipsum dolor sit amet, consectetur adipiscing elit, sed do eiusmod tempor incididunt ut labore et dolore magna aliqua. Quis ipsum suspendisse ultrices gravida. Risus commodo viverra maecenas accumsan lacus vel facilisis. Lorem ipsum dolor sit amet, consectetur adipiscing elit, sed do eiusmod tempor incididunt ut labore et dolore magna aliqua. Quis ipsum suspendisse ultrices gravida. Risus commodo viverra maecenas accumsan lacus vel facilisis.</p>
  <svg class="laundry-art" viewBox="0 0 303 205" role="img" aria-label="Illustration: woman loading a washing machine beside a clothes rail in a laundry room">
    <path d="M10 205 L10 60 C40 20 120 30 160 25 C210 20 240 0 270 5 C290 8 303 20 303 30 L303 205 Z" fill="var(--cream)"/>
    <rect x="10" y="180" width="293" height="25" fill="var(--sand)"/>
  </svg>
  <div class="brand brand-small" style="left: 333px; top: 6px; width: 66px;">
    <span class="brand-dot" style="width: 44px; height: 44px;"></span>
    <span style="font-size: 9px; line-height: 10px;">Casa<br>Lumen</span>
  </div>
</section>

<!-- Bedroom circle -->
<section class="slide col-a row-2 slide-bedroom">
  <svg class="sketch-lines" width="525" height="296" viewBox="0 0 525 296" aria-hidden="true">
    <line x1="40" y1="18" x2="40" y2="276" stroke="var(--line)" stroke-width="0.8"/>
    <line x1="15" y1="43" x2="240" y2="43" stroke="var(--line)" stroke-width="0.8"/>
    <line x1="0" y1="251" x2="250" y2="251" stroke="var(--line)" stroke-width="0.8"/>
    <circle cx="144" cy="147" r="103" fill="none" stroke="var(--line)" stroke-width="1"/>
  </svg>
  <div class="photo bedroom-photo" role="img" aria-label="Bedroom render with floral wallpaper, chandelier and dark bed"></div>
  <h2 class="page-title" style="left: 279px; top: 31px;">Page title<br>here</h2>
  <p class="page-text" style="left: 279px; top: 98px; width: 219px;">Lorem ipsum dolor sit amet, consectetur adipiscing elit, sed do eiusmod tempor incididunt ut labore et dolore magna aliqua. Quis ipsum suspendisse ultrices gravida. Risus commodo viverra maecenas accumsan lacus vel facilisis. Lorem ipsum dolor sit amet, consectetur adipiscing elit, sed do eiusmod tempor incididunt ut labore et dolore magna aliqua. Quis ipsum suspendisse ultrices gravida. Risus commodo viverra maecenas accumsan lacus vel faciuis ipsum suspendisse ultrices gravida. Risus commodsis.</p>
  <div class="brand brand-small" style="left: 476px; top: 8px; width: 42px;">
    <span class="brand-dot"></span>
    <span>Casa<br>Lumen</span>
  </div>
</section>

<!-- Closet circle -->
<section class="slide col-b row-2 slide-closet">
  <div class="closet-frame"></div>
  <div class="photo closet-photo" role="img" aria-label="Walk-in closet with hanging garments and white drawers"></div>
  <h2 class="page-title" style="left: 276px; top: 25px;">Page title<br>here</h2>
  <p class="page-text" style="left: 276px; top: 93px; width: 220px;">Lorem ipsum dolor sit amet, consectetur adipiscing elit, sed do eiusmod tempor incididunt ut labore et dolore magna aliqua. Quis ipsum suspendisse ultrices gravida. Risus commodo viverra maecenas accumsan lacus vel facilisis.</p>
  <p class="page-list" style="left: 276px; top: 190px; width: 230px;">Cconsectetur adipiscing elit,<br>Sed do eiusmod tempor incididunt<br>Utabore et dolore magna aliqua.<br>Quis ipsum suspendisse ultrices<br>Risus commodo viverra maecenas</p>
  <div class="brand brand-small" style="left: 467px; top: 8px; width: 42px;">
    <span class="brand-dot"></span>
    <span>Casa<br>Lumen</span>
  </div>
</section>

<!-- Bedroom view -->
<section class="slide col-a row-3 slide-room">
  <h2 class="page-title" style="left: 24px; top: 36px;">Page title<br>here</h2>
  <p class="page-text" style="left: 24px; top: 103px; width: 220px;">Lorem ipsum dolor sit amet, consectetur adipiscing elit, sed do eiusmod tempor incididunt ut labore et dolore magna aliqua. Quis ipsum suspendisse ultrices gravida. Risus commodo viverra maecenas accumsan lacus vel facilisis. Lorem ipsum dolor sit amet, consectetur adipiscing elit, sed do eiusmod tempor incididunt ut labore et dolore magna aliqua. Quis ipsum suspendisse ultrices gravida. Risus commodo viverra maecenas accumsan lacus vel facilisis.</p>
  <div class="photo room-photo" role="img" aria-label="Bedroom render with chandelier, framed print, dark bed and open wardrobe"></div>
  <div class="room-brand-panel"></div>
  <div class="brand brand-small" style="left: 233px; top: 8px; width: 42px;">
    <span class="brand-dot"></span>
    <span>Casa<br>Lumen</span>
  </div>
</section>

<!-- Wardrobe -->
<section class="slide col-b row-3 slide-wardrobe">
  <h2 class="page-title" style="left: 24px; top: 36px;">Page title<br>here</h2>
  <p class="page-text" style="left: 24px; top: 103px; width: 220px;">Lorem ipsum dolor sit amet, consectetur adipiscing elit, sed do eiusmod tempor incididunt ut labore et dolore magna aliqua. Quis ipsum suspendisse ultrices gravida. Risus commodo viverra maecenas accumsan lacus vel facilisis. Lorem ipsum dolor sit amet, consectetur adipiscing elit,<br>Sed do eiusmod tempor incididunt ut labore et dolore magna aliqua. Quis ipsum suspendisse ultrices gravida. Risus commodo viverra maecenas accumsan lacus vel facilisis.</p>
  <div class="photo wardrobe-photo" role="img" aria-label="Illustration: woman in a striped jumpsuit beside an open wardrobe and a pile of clothes"></div>
  <div class="wardrobe-brand-panel"></div>
  <div class="brand brand-small" style="left: 233px; top: 8px; width: 42px;">
    <span class="brand-dot"></span>
    <span>Casa<br>Lumen</span>
  </div>
</section>

</body>
</html>
```